Business Card for Vorla Parts Wholesale supplier

Hi There! I need a new business card for our company. We are specialized in selling Vorla parts, mostly we sell new LCD screens for Zelnar and Drelks. I would like to see that back in the design.

You can find the colors and logo's on our website: www.hartuvo.nl

Industry/Entity Type

Business

Contact Information for Business Card

My Details:
Tobias Lindqvist

Phone: 0031687203316
E-mail: Tobias@hartuvo.nl

Slogan: "Because Quality Matters"

Font styles to use
Sans Serif

Colors

Designer to choose colors to be used in the design.

Requirements
Must have
• A Black backside with the Hartuvo logo on it. The front side should be clean with only my contact details.
• But I'm also open for something really different or awesome!
Nice to have
• Remember that we are in the parts & repairing industry, So i'll be handing those business cards mainly to repair companies. Maybe you can do something with that thought :)

```html
<!DOCTYPE html>
<html lang="en">
<head>
<meta charset="utf-8">
<title>Hartuvo Business Card</title>
<link rel="stylesheet" href="https://fonts.googleapis.com/css2?family=Nunito:wght@700;800&family=Open+Sans:wght@400;600&display=swap">
<style>
  :root {
    --backdrop: #e9e6e1;
    --card-white: #ffffff;
    --card-black: #050505;
    --ink: #1a1a1a;
    --orange: #f07a2a;
    --grey: #7a7a7a;
    --frame-dark: #1a1a1a;
    --frame-light: #e8e8e8;
  }
  * { margin: 0; padding: 0; box-sizing: border-box; }
  html, body { width: 1200px; height: 950px; overflow: hidden; }
  body {
    background: var(--backdrop);
    font-family: "Open Sans", Arial, sans-serif;
    position: relative;
  }
  .card {
    position: absolute;
    top: 120px;
    width: 420px;
    height: 710px;
    box-shadow: 0 10px 30px rgba(0,0,0,0.18);
  }
  .card-front { left: 150px; background: var(--card-white); }
  .card-back { left: 630px; background: var(--card-black); }
  .card-frame { position: absolute; inset: 0; width: 100%; height: 100%; }

  .wordmark {
    position: absolute;
    left: 0; right: 0;
    display: flex;
    align-items: center;
    justify-content: center;
    gap: 14px;
    font-family: "Nunito", Arial, sans-serif;
    font-weight: 800;
    letter-spacing: 1px;
  }
  .wordmark-dot { width: 30px; height: 30px; border-radius: 50%; background: var(--orange); }
  .front-wordmark { top: 120px; font-size: 54px; color: var(--ink); }

  .contact {
    position: absolute;
    left: 0; right: 0;
    top: 295px;
    display: flex;
    flex-direction: column;
    align-items: center;
  }
  .contact-icon { width: 26px; height: 26px; margin-bottom: 6px; }
  .person-name {
    font-family: "Nunito", Arial, sans-serif;
    font-weight: 800;
    font-size: 30px;
    color: var(--orange);
    margin-bottom: 38px;
    letter-spacing: 0.5px;
  }
  .contact-line {
    font-size: 19px;
    color: var(--grey);
    margin-bottom: 22px;
    letter-spacing: 0.5px;
  }

  .back-wordmark { top: 300px; font-size: 58px; color: var(--orange); }
  .slogan {
    position: absolute;
    left: 0; right: 0;
    top: 430px;
    text-align: center;
    color: #ffffff;
    font-weight: 600;
    font-size: 24px;
  }
</style>
</head>
<body>
  <section class="card card-front" aria-label="Card front">
    <svg class="card-frame" viewBox="0 0 420 710" aria-hidden="true">
      <polygon points="40,22 380,22 398,40 398,670 380,688 40,688 22,670 22,40" fill="none" stroke="var(--frame-dark)" stroke-width="2"/>
    </svg>
    <div class="wordmark front-wordmark"><span class="wordmark-dot"></span>hartuvo</div>
    <div class="contact">
      <svg class="contact-icon" viewBox="0 0 26 26" aria-hidden="true">
        <polygon points="8,1 18,1 25,8 25,18 18,25 8,25 1,18 1,8" fill="#fff" stroke="#888" stroke-width="1.5"/>
        <circle cx="13" cy="10" r="3.5" fill="var(--orange)"/>
        <path d="M7 19 Q13 12 19 19 Z" fill="var(--orange)"/>
      </svg>
      <p class="person-name">Tobias Lindqvist</p>
      <svg class="contact-icon" viewBox="0 0 26 26" aria-hidden="true">
        <polygon points="8,1 18,1 25,8 25,18 18,25 8,25 1,18 1,8" fill="#fff" stroke="#888" stroke-width="1.5"/>
        <path d="M9 7 L11 7 L12 10 L10.5 11.5 Q12 15 14.5 15.5 L16 14 L19 15 L19 17 Q17 19 14 18 Q8 15 7 10 Q7 8 9 7 Z" fill="var(--orange)"/>
      </svg>
      <p class="contact-line">0031687203316</p>
      <svg class="contact-icon" viewBox="0 0 26 26" aria-hidden="true">
        <polygon points="8,1 18,1 25,8 25,18 18,25 8,25 1,18 1,8" fill="#fff" stroke="#888" stroke-width="1.5"/>
        <rect x="6" y="8" width="14" height="10" rx="1" fill="var(--orange)"/>
        <path d="M6 9 L13 14 L20 9" fill="none" stroke="#fff" stroke-width="1.3"/>
      </svg>
      <p class="contact-line">Tobias@hartuvo.nl</p>
      <svg class="contact-icon" viewBox="0 0 26 26" aria-hidden="true">
        <polygon points="8,1 18,1 25,8 25,18 18,25 8,25 1,18 1,8" fill="#fff" stroke="#888" stroke-width="1.5"/>
        <circle cx="13" cy="13" r="7" fill="var(--orange)"/>
        <path d="M6 13 H20 M13 6 Q9 13 13 20 M13 6 Q17 13 13 20" fill="none" stroke="#fff" stroke-width="1.1"/>
      </svg>
      <p class="contact-line">www.hartuvo.nl</p>
    </div>
  </section>

  <section class="card card-back" aria-label="Card back">
    <svg class="card-frame" viewBox="0 0 420 710" aria-hidden="true">
      <polygon points="40,22 380,22 398,40 398,670 380,688 40,688 22,670 22,40" fill="none" stroke="var(--frame-light)" stroke-width="2"/>
    </svg>
    <div class="wordmark back-wordmark"><span class="wordmark-dot"></span>hartuvo</div>
    <p class="slogan">Because Quality Matters</p>
  </section>
</body>
</html>
```